Business cards for Harbourline Supply Pty Ltd that import building products into Australia from China
Target Market(s)
Business to Business
Industry/Entity Type
Business
Contact Information for Business Card
Front: Logo and Business Name
Rear:
Desmond Varrick
General Manager
Mobile: 0427 561 394
email: dessie@harbourlinesupply.com.au
alternative email: dessie@outbackworks.com.au
web: www.harbourlinesupply.com.au
Calloway, Westmere and Durnfield
Colors
ec1f27
fbee3d

```html
<!DOCTYPE html>
<html lang="en">
<head>
<meta charset="UTF-8">
<title>Harbourline Supply Pty Ltd — Business Cards</title>
<link href="https://fonts.googleapis.com/css2?family=Saira:wght@400;500;700&display=swap" rel="stylesheet">
<style>
  :root {
    --brand-red: #ec1f27;
    --brand-yellow: #fbee3d;
    --ink: #1c1c1c;
    --paper: #ffffff;
    --backdrop: #bfbdbe;
  }
  * { margin: 0; padding: 0; box-sizing: border-box; }
  html, body { width: 1200px; height: 900px; overflow: hidden; }
  body {
    background: var(--backdrop);
    position: relative;
    font-family: "Saira", "Arial", sans-serif;
    color: var(--ink);
  }
  .card {
    position: absolute;
    top: 270px;
    width: 457px;
    height: 283px;
    border-radius: 14px;
    overflow: hidden;
  }
  .card--contact { left: 137px; background: var(--paper); }
  .card--brand {
    left: 626px;
    background: linear-gradient(180deg, var(--brand-yellow) 0%, #f6a23a 45%, var(--brand-red) 100%);
  }

  .person { position: absolute; left: 26px; top: 24px; }
  .person__name { font-size: 18.5px; font-weight: 700; letter-spacing: 0.2px; line-height: 1.1; }
  .person__first { color: var(--brand-red); }
  .person__role { font-size: 12.5px; font-weight: 400; margin-top: 3px; }

  .wordmark {
    position: absolute;
    display: flex;
    flex-direction: column;
    align-items: center;
    text-align: center;
  }
  .wordmark__square { width: 44px; height: 44px; margin-bottom: 10px; }
  .wordmark__name { font-weight: 700; line-height: 1.05; }
  .card--contact .wordmark { left: 232px; top: 30px; width: 200px; }
  .card--contact .wordmark__square { background: var(--brand-red); }
  .card--contact .wordmark__name { color: var(--brand-red); font-size: 22px; }
  .card--brand .wordmark { left: 104px; top: 74px; width: 250px; }
  .card--brand .wordmark__square { background: var(--paper); width: 52px; height: 52px; }
  .card--brand .wordmark__name { color: var(--paper); font-size: 27px; }

  .contacts { position: absolute; left: 26px; top: 183px; list-style: none; }
  .contacts li {
    display: flex; align-items: center; gap: 8px;
    font-size: 13px; height: 19px;
  }
  .contacts svg { width: 12px; height: 12px; fill: var(--brand-red); flex: none; }

  .locations {
    position: absolute; right: 34px; top: 219px;
    text-align: right; font-size: 13px; line-height: 21px;
  }

  .stripe { position: absolute; bottom: 0; height: 14px; }
  .stripe--red { left: 0; width: 218px; background: var(--brand-red); }
  .stripe--yellow { left: 226px; right: 0; background: #eadc16; }
</style>
</head>
<body>

<section class="card card--contact" aria-label="Business card, contact side">
  <div class="person">
    <div class="person__name"><span class="person__first">DESMOND</span> VARRICK</div>
    <div class="person__role">General Manager</div>
  </div>

  <div class="wordmark">
    <div class="wordmark__square"></div>
    <div class="wordmark__name">Harbourline Supply<br>Pty Ltd</div>
  </div>

  <ul class="contacts">
    <li>
      <svg viewBox="0 0 12 12" aria-hidden="true"><path d="M1 4.5C1 2.5 3.5 1.5 6 1.5S11 2.5 11 4.5L9 5 8.5 3.6h-5L3 5z"/><path d="M3 6.5h6l1 4H2z"/></svg>
      0427 561 394
    </li>
    <li>
      <svg viewBox="0 0 12 12" aria-hidden="true"><path d="M1 2.5h10v7H1z M1.8 3.2 6 6.6l4.2-3.4z" fill-rule="evenodd"/></svg>
      dessie@harbourlinesupply.com.au
    </li>
    <li>
      <svg viewBox="0 0 12 12" aria-hidden="true"><path d="M1 2.5h10v7H1z M1.8 3.2 6 6.6l4.2-3.4z" fill-rule="evenodd"/></svg>
      dessie@outbackworks.com.au
    </li>
    <li>
      <svg viewBox="0 0 12 12" aria-hidden="true"><circle cx="6" cy="6" r="5"/><path d="M3.5 4.5 5.5 3.5 6 5 4.5 7z M7 7l2-0.5-0.5 2z" fill="#fff"/></svg>
      www.harbourlinesupply.com.au
    </li>
  </ul>

  <div class="locations">Calloway,<br>Westmere and Durnfield</div>

  <div class="stripe stripe--red"></div>
  <div class="stripe stripe--yellow"></div>
</section>

<section class="card card--brand" aria-label="Business card, brand side">
  <div class="wordmark">
    <div class="wordmark__square"></div>
    <div class="wordmark__name">Harbourline Supply<br>Pty Ltd</div>
  </div>
</section>

</body>
</html>
```